Bran-well Tide Gate Custom Brokers Limited

Name: Lorvina Hadcott
Title: Customs Broker
Address: Shop 9 Ferncliff Commercial Complex
207-209 Mulgrave Road
Kingston 8
Telephone: (876)
Email: tidegatewell@mailbrook.example

```html
<!DOCTYPE html>
<html lang="en">
<head>
<meta charset="utf-8">
<title>Bran-well Tide Gate Custom Brokers Ltd. — Business Card</title>
<link rel="stylesheet" href="https://fonts.googleapis.com/css2?family=Poppins:wght@400;500;600;700&display=swap">
<style>
  :root {
    --page: #e9ebef;
    --card-navy: #0b2a52;
    --accent-gold: #f0a90c;
    --ink-white: #ffffff;
    --card-radius: 34px;
  }
  * { margin: 0; padding: 0; box-sizing: border-box; }
  html, body {
    width: 1200px;
    height: 1189px;
    overflow: hidden;
    background: var(--page);
    font-family: "Poppins", sans-serif;
  }
  .sheet {
    position: relative;
    width: 1200px;
    height: 1189px;
  }
  .card {
    position: absolute;
    left: 150px;
    width: 900px;
    height: 514px;
    background: var(--card-navy);
    border-radius: var(--card-radius);
    color: var(--ink-white);
    box-shadow: 0 10px 30px rgba(11, 42, 82, 0.25);
  }
  .card--front { top: 60px; }
  .card--back { top: 615px; }

  .brand {
    position: absolute;
    display: flex;
    align-items: center;
    gap: 18px;
  }
  .brand__dot {
    width: 46px;
    height: 46px;
    border-radius: 50%;
    background: var(--accent-gold);
    flex: none;
  }
  .brand__name {
    font-weight: 600;
    color: var(--ink-white);
    line-height: 1.15;
    letter-spacing: 0.5px;
  }
  .card--front .brand {
    left: 50%;
    top: 50%;
    transform: translate(-50%, -50%);
  }
  .card--front .brand__name { font-size: 38px; }
  .card--back .brand {
    left: 480px;
    top: 150px;
  }
  .card--back .brand__name { font-size: 28px; }

  .holder {
    position: absolute;
    left: 70px;
    top: 86px;
  }
  .holder__name {
    font-size: 27px;
    font-weight: 700;
    letter-spacing: 0.5px;
    text-transform: uppercase;
    line-height: 1.1;
  }
  .holder__title {
    font-size: 22px;
    font-weight: 500;
    color: var(--accent-gold);
    margin-top: 2px;
  }
  .address {
    position: absolute;
    left: 70px;
    top: 210px;
    font-size: 20px;
    font-weight: 500;
    line-height: 1.35;
  }
  .contacts {
    position: absolute;
    left: 70px;
    top: 382px;
    list-style: none;
    font-size: 21px;
    font-weight: 500;
  }
  .contacts__item {
    display: flex;
    align-items: center;
    gap: 12px;
    margin-bottom: 8px;
  }
  .contacts__icon {
    width: 28px;
    height: 28px;
    flex: none;
  }
</style>
</head>
<body>
<main class="sheet">
  <section class="card card--front" aria-label="Card front">
    <div class="brand">
      <span class="brand__dot"></span>
      <span class="brand__name">Bran-well Tide Gate<br>Custom Brokers Ltd.</span>
    </div>
  </section>

  <section class="card card--back" aria-label="Card back">
    <div class="holder">
      <h1 class="holder__name">Lorvina Hadcott</h1>
      <p class="holder__title">Customs Broker</p>
    </div>
    <address class="address" style="font-style: normal;">
      Shop 9 Ferncliff<br>
      Commercial Complex<br>
      207-209 Mulgrave Road<br>
      Kingston 8
    </address>
    <ul class="contacts">
      <li class="contacts__item">
        <svg class="contacts__icon" viewBox="0 0 28 28" aria-hidden="true">
          <circle cx="14" cy="14" r="14" fill="#f0a90c"/>
          <rect x="9" y="7" width="10" height="14" rx="2" fill="none" stroke="#0b2a52" stroke-width="2"/>
          <line x1="12.5" y1="18" x2="15.5" y2="18" stroke="#0b2a52" stroke-width="1.6"/>
        </svg>
        <span>(876) 555 0142</span>
      </li>
      <li class="contacts__item">
        <svg class="contacts__icon" viewBox="0 0 28 28" aria-hidden="true">
          <circle cx="14" cy="14" r="14" fill="#f0a90c"/>
          <rect x="7" y="9" width="14" height="10" rx="1" fill="none" stroke="#0b2a52" stroke-width="1.8"/>
          <polyline points="7,9 14,15 21,9" fill="none" stroke="#0b2a52" stroke-width="1.8"/>
        </svg>
        <span>tidegatewell@mailbrook.example</span>
      </li>
    </ul>
    <div class="brand">
      <span class="brand__dot"></span>
      <span class="brand__name">Bran-well Tide Gate<br>Custom Brokers Ltd.</span>
    </div>
  </section>
</main>
</body>
</html>
```